Brake Test Training for Coal Mining

We offer Brake Test Training for Coal Mine workers. It's a legislative requirement that workers who are tasked with performing brake testing have certain competencies to do so. We test Light Vehicles and trailers, Heavy Vehicles and Mobile Mining Equipment like Graders, Scrapers and Dump Trucks.

```html
<!DOCTYPE html>
<html lang="en">
<head>
<meta charset="utf-8">
<title>Brake Test Training</title>
<link href="https://fonts.googleapis.com/css2?family=Anton&family=Montserrat:wght@500;600;800&display=swap" rel="stylesheet">
<style>
  :root {
    --navy: #1f2a5c;
    --navy-deep: #18224d;
    --yellow: #fbb416;
    --white: #ffffff;
    --ink: #14193a;
  }
  html, body { margin: 0; padding: 0; overflow: hidden; background: var(--white); }
  .billboard {
    position: relative;
    width: 1200px;
    height: 815px;
    overflow: hidden;
    background: radial-gradient(circle at 45% 55%, #2b3a78 0%, var(--navy) 45%, var(--navy-deep) 100%);
    font-family: "Montserrat", sans-serif;
  }
  .brand-tab {
    position: absolute;
    left: 0; top: 0;
    width: 500px; height: 150px;
    background: var(--white);
    border-bottom-right-radius: 75px;
    display: flex;
    align-items: center;
    gap: 18px;
    padding-left: 48px;
    box-sizing: border-box;
  }
  .brand-dot {
    width: 56px; height: 56px;
    border-radius: 50%;
    background: var(--navy);
    flex: none;
  }
  .brand-name {
    font-family: "Montserrat", sans-serif;
    font-weight: 800;
    font-size: 30px;
    letter-spacing: 1px;
    color: var(--navy);
    line-height: 1.1;
  }
  .hero-photo {
    position: absolute;
    left: 0; top: 150px;
    width: 580px; height: 560px;
    background: linear-gradient(160deg, #8a8fa8 0%, #b59a63 35%, #c9a23a 55%, #5e5446 80%, #3a3a48 100%);
    -webkit-mask-image: linear-gradient(90deg, #000 80%, transparent 100%);
    mask-image: linear-gradient(90deg, #000 80%, transparent 100%);
  }
  .headline {
    position: absolute;
    right: 40px; top: 40px;
    margin: 0;
    text-align: right;
    font-family: "Anton", sans-serif;
    font-weight: 400;
    color: var(--yellow);
    font-size: 150px;
    line-height: 0.98;
    letter-spacing: 1px;
  }
  .headline span { display: block; }
  .services {
    position: absolute;
    left: 560px; right: 40px; top: 378px;
    margin: 0;
    color: var(--white);
    font-weight: 500;
    font-size: 33px;
    line-height: 1.25;
    text-transform: uppercase;
    text-align: center;
    letter-spacing: 0.5px;
  }
  .equipment {
    position: absolute;
    left: 560px; right: 40px; top: 555px;
    margin: 0; padding: 0;
    list-style: none;
    display: flex;
    flex-wrap: wrap;
    justify-content: center;
    gap: 14px 28px;
    color: var(--yellow);
    font-weight: 800;
    font-size: 40px;
    text-transform: uppercase;
  }
  .equipment li { display: flex; align-items: center; gap: 12px; }
  .equipment .divider { width: 3px; height: 40px; background: var(--yellow); }
  .equipment .wide { flex-basis: 100%; justify-content: center; }
  .tick { width: 40px; height: 40px; flex: none; }
  .contact-bar {
    position: absolute;
    left: 0; bottom: 0;
    width: 1200px; height: 110px;
    background: var(--white);
  }
  .phone-block {
    position: absolute;
    left: 0; top: 0;
    width: 620px; height: 110px;
    background: var(--yellow);
    clip-path: polygon(0 0, 570px 0, 620px 110px, 0 110px);
    display: flex;
    align-items: center;
    gap: 16px;
    padding-left: 48px;
    box-sizing: border-box;
  }
  .phone-icon { width: 46px; height: 46px; flex: none; }
  .phone-number {
    font-weight: 800;
    font-size: 62px;
    color: var(--navy);
    letter-spacing: 1px;
  }
  .address {
    position: absolute;
    left: 640px; right: 30px; top: 0; height: 110px;
    display: flex; align-items: center; justify-content: center;
    font-weight: 500;
    font-size: 30px;
    color: var(--ink);
  }
</style>
</head>
<body>
<main class="billboard">
  <header class="brand-tab">
    <span class="brand-dot"></span>
    <span class="brand-name">CENTRAL PLANT SKILLS</span>
  </header>

  <div class="hero-photo" role="img" aria-label="Large yellow mining dump truck on a haul road in front of a spoil heap"></div>

  <h1 class="headline"><span>BRAKE TEST</span><span>TRAINING</span></h1>

  <p class="services">We test light vehicles &amp; trailers, heavy vehicles &amp; mobile mining equipment</p>

  <ul class="equipment">
    <li><svg class="tick" viewBox="0 0 40 40"><circle cx="20" cy="20" r="19" fill="var(--yellow)"/><path d="M11 21l6 6 12-13" fill="none" stroke="var(--navy)" stroke-width="4.5" stroke-linecap="round" stroke-linejoin="round"/></svg>Graders</li>
    <li class="divider" aria-hidden="true"></li>
    <li><svg class="tick" viewBox="0 0 40 40"><circle cx="20" cy="20" r="19" fill="var(--yellow)"/><path d="M11 21l6 6 12-13" fill="none" stroke="var(--navy)" stroke-width="4.5" stroke-linecap="round" stroke-linejoin="round"/></svg>Scrapers</li>
    <li class="wide"><svg class="tick" viewBox="0 0 40 40"><circle cx="20" cy="20" r="19" fill="var(--yellow)"/><path d="M11 21l6 6 12-13" fill="none" stroke="var(--navy)" stroke-width="4.5" stroke-linecap="round" stroke-linejoin="round"/></svg>Dump Trucks</li>
  </ul>

  <footer class="contact-bar">
    <div class="phone-block">
      <svg class="phone-icon" viewBox="0 0 24 24"><path fill="var(--navy)" d="M6.6 10.8a15.1 15.1 0 0 0 6.6 6.6l2.2-2.2a1 1 0 0 1 1-.25 11.4 11.4 0 0 0 3.6.57 1 1 0 0 1 1 1V20a1 1 0 0 1-1 1A17 17 0 0 1 3 4a1 1 0 0 1 1-1h3.5a1 1 0 0 1 1 1c0 1.25.2 2.45.57 3.57a1 1 0 0 1-.25 1z"/></svg>
      <span class="phone-number">1300 555 018</span>
    </div>
    <address class="address">24 Ridgeline Rd, Coalfield. Qld 4799</address>
  </footer>
</main>
</body>
</html>
```